Business card for Luxury Portable Restroom Trailer company

We are a Luxury Portable Restroom Trailer Company Called FALCRIDGE HIRES. Based in Orange County California. We provide portable restroom trailers for events, such as, Weddings, Concerts, Charity events, Sporting events, Tournaments, Corporate events, ect. We rent and Sell the Luxury restrooms. Our colors are white, grey, and Orange. As you will see in the logo we uploaded.
There are 2 people in the company so the names and titles will change for the 3 people but card will remain the same. Here is the information for each Person: Dwight Penner CFO 555 318-0476
next Person: Leon Marchetti VP 555 318-0476
Next Person: Owen Marchetti CEO 555 318-0476
Information to include on the card: Luxury Restroom Trailers Rental and Sales. Weddings, Concerts, Charity, Sporting and Corp. Events.

```html
<!DOCTYPE html>
<html lang="en">
<head>
<meta charset="utf-8">
<title>FALCRIDGE HIRES – Business Cards</title>
<link rel="stylesheet" href="https://fonts.googleapis.com/css2?family=Montserrat:wght@400;700;800&display=swap">
<style>
  :root {
    --stage: #2b2b2b;
    --card: #181818;
    --orange: #f26f24;
    --grey: #58595b;
    --white: #f4f4f4;
  }
  * { box-sizing: border-box; margin: 0; padding: 0; }
  html, body { width: 1200px; height: 853px; overflow: hidden; }
  body {
    background: var(--stage);
    font-family: "Montserrat", Arial, sans-serif;
    display: flex;
    align-items: center;
    justify-content: center;
    gap: 40px;
  }
  .card {
    position: relative;
    width: 540px;
    height: 309px;
    background: var(--card);
    border-radius: 22px;
    box-shadow: 0 14px 30px rgba(0,0,0,.45);
    overflow: hidden;
  }

  /* contact side */
  .card-contact { display: flex; padding: 26px 24px 22px 28px; }
  .contact-column { width: 230px; display: flex; flex-direction: column; }
  .brand-small {
    color: var(--orange);
    font-weight: 800;
    font-size: 19px;
    letter-spacing: .5px;
    margin-bottom: 18px;
  }
  .person { margin-bottom: 10px; }
  .person-name { color: var(--orange); font-weight: 700; font-size: 17px; line-height: 1.2; }
  .person-title { color: var(--white); font-size: 12px; margin: 2px 0 2px 12px; }
  .person-phone {
    color: var(--white);
    font-size: 12px;
    margin-left: 12px;
    display: flex;
    align-items: center;
    gap: 6px;
  }
  .person-phone svg { width: 12px; height: 12px; fill: var(--orange); }
  .emblem {
    flex: 1;
    display: flex;
    align-items: center;
    justify-content: center;
  }
  .emblem-ring {
    width: 232px;
    height: 232px;
    border: 10px solid var(--orange);
    border-radius: 50%;
    display: flex;
    align-items: center;
    justify-content: center;
    text-align: center;
    color: var(--orange);
    font-weight: 800;
    font-size: 26px;
    line-height: 1.15;
  }

  /* brand side */
  .card-brand {
    display: flex;
    flex-direction: column;
    align-items: center;
    justify-content: center;
    padding: 30px 28px;
  }
  .brand-large {
    color: var(--orange);
    font-weight: 800;
    font-size: 46px;
    letter-spacing: 1px;
    margin-top: 20px;
  }
  .tagline {
    margin-top: 54px;
    color: var(--white);
    font-size: 13.5px;
    text-align: center;
    line-height: 1.45;
  }
</style>
</head>
<body>

  <section class="card card-contact" aria-label="Contact side">
    <div class="contact-column">
      <div class="brand-small">FALCRIDGE HIRES</div>

      <div class="person">
        <div class="person-name">Dwight Penner</div>
        <div class="person-title">CFO</div>
        <div class="person-phone">
          <svg viewBox="0 0 24 24" aria-hidden="true"><path d="M6.6 10.8a15.1 15.1 0 0 0 6.6 6.6l2.2-2.2a1 1 0 0 1 1-.25 11.4 11.4 0 0 0 3.6.57 1 1 0 0 1 1 1V20a1 1 0 0 1-1 1A17 17 0 0 1 3 4a1 1 0 0 1 1-1h3.5a1 1 0 0 1 1 1c0 1.25.2 2.45.57 3.6a1 1 0 0 1-.25 1z"/></svg>
          555 318-0476
        </div>
      </div>

      <div class="person">
        <div class="person-name">Leon Marchetti</div>
        <div class="person-title">VP</div>
        <div class="person-phone">
          <svg viewBox="0 0 24 24" aria-hidden="true"><path d="M6.6 10.8a15.1 15.1 0 0 0 6.6 6.6l2.2-2.2a1 1 0 0 1 1-.25 11.4 11.4 0 0 0 3.6.57 1 1 0 0 1 1 1V20a1 1 0 0 1-1 1A17 17 0 0 1 3 4a1 1 0 0 1 1-1h3.5a1 1 0 0 1 1 1c0 1.25.2 2.45.57 3.6a1 1 0 0 1-.25 1z"/></svg>
          555 318-0476
        </div>
      </div>

      <div class="person">
        <div class="person-name">Owen Marchetti</div>
        <div class="person-title">CEO</div>
        <div class="person-phone">
          <svg viewBox="0 0 24 24" aria-hidden="true"><path d="M6.6 10.8a15.1 15.1 0 0 0 6.6 6.6l2.2-2.2a1 1 0 0 1 1-.25 11.4 11.4 0 0 0 3.6.57 1 1 0 0 1 1 1V20a1 1 0 0 1-1 1A17 17 0 0 1 3 4a1 1 0 0 1 1-1h3.5a1 1 0 0 1 1 1c0 1.25.2 2.45.57 3.6a1 1 0 0 1-.25 1z"/></svg>
          555 318-0476
        </div>
      </div>
    </div>

    <div class="emblem">
      <div class="emblem-ring">FALCRIDGE<br>HIRES</div>
    </div>
  </section>

  <section class="card card-brand" aria-label="Brand side">
    <div class="brand-large">FALCRIDGE HIRES</div>
    <p class="tagline">
      Luxury Restroom Trailers Rental and Sales.<br>
      Weddings, Concerts, Charity, Sporting and Corp. Events.
    </p>
  </section>

</body>
</html>
```